PostCard Design Project

I am making a mailing postcard
I am having the mailing printed using 4 color foil on certain parts.
I am looking for a design that maximizes the foil process where certain parts are done in foil to grab the customers attention (example: if there is a car on the postcard the headlights would be done in foil) .
I am targeting some industries, (auto, real estate, medical, beauty) I would like the post card to have examples of postcard ideas for 2 or 3 of these industries.
specs:
the postcard should be atleast 6.5x9 up to 8.5x11, I don't want to restrict the space for the creative as I don't want everything to look like a huge mess. both sides will be used.
the piece is a direct mail piece so it has to meet requirements of https://www.mailvantor.com/business/pdf/quick-reference-guide.pdf
text will be
"business with no limits, meet mailing with no addresses, gain new customers through "Open Porch Route Drop" reach new customers at their home without needing their address. "
I also want some current print specials I am running included.
-double your order FREE (order 500 business cards and get 1000)
-250 100lb gloss stock brochures 99.00
-business packages (cards, envelopes and letterhead) 299
-1000 flyers 140.40
-5000 postcards 179.99
A list of services
banners
booklets
brochures
business cards
calendars
catalogs
CD/DVD packages
envelopes
event tickets
flyers
hangtags
postcards
posters
presentation folders
rack cards
labels
table tents
window cling and decal
"order 24/7 orders@inkwillow.com" must be included
my logo is InkWillow will be supplied later
ive received some great designs. however Im looking for something a little more modern like some zorvel would put out. if the amount of words is too much please feel free to edit. also an idea i had for the list of services i offer is to have it transparent yet readable as the background of the postcard some small some big but covering the entire backgroud. you can then design on top of that with other thing. just an early morning thought
Reason: I have uploaded a sketch of my idea, please take time to look at it for an accurate depiction of what im looking for. feel free to add elements that make it pop off the page
Reason: We are getting close i will be providing feed back today

```html
<!DOCTYPE html>
<html lang="en">
<head>
<meta charset="utf-8">
<title>InkWillow Mailing Postcard</title>
<link rel="stylesheet" href="https://fonts.googleapis.com/css2?family=Archivo+Black&family=Arimo:wght@400;700&display=swap">
<style>
  :root {
    --stage: #e9e6e1;
    --card-black: #0d0d0d;
    --card-charcoal: #2a2a2a;
    --shine-yellow: #f4e60f;
    --text-white: #ffffff;
    --text-soft: #e6e6e6;
    --word-grey: #6a6a6a;
    --word-light: #7a7a7a;
    --band-dark: #151515;
    --sample-white: #f7f7f7;
    --sample-blue: #1f5f7a;
    --stamp-ink: #222222;
  }
  * { box-sizing: border-box; margin: 0; padding: 0; }
  html, body {
    width: 1200px; height: 900px; overflow: hidden;
    background: var(--stage);
  }
  .stage {
    width: 1200px; height: 900px;
    display: flex; align-items: center; justify-content: center; gap: 24px;
  }
  .postcard {
    position: relative; width: 570px; height: 380px; overflow: hidden;
    background: radial-gradient(ellipse at 60% 45%, var(--card-charcoal) 0%, var(--card-black) 70%);
    box-shadow: 0 10px 28px rgba(0,0,0,.35);
    font-family: "Arimo", Arial, sans-serif;
    color: var(--text-white);
  }

  /* Front */
  .samples { position: absolute; right: 0; top: 0; width: 330px; height: 215px; }
  .sample { position: absolute; }
  .sample--wedding {
    left: 10px; top: 78px; width: 118px; height: 122px;
    background: linear-gradient(160deg, var(--sample-white), #d9d9d9);
  }
  .sample--beauty {
    left: 130px; top: 0; width: 150px; height: 80px;
    background: linear-gradient(120deg, var(--sample-white) 40%, #d8b89c 100%);
  }
  .sample--auto {
    left: 128px; top: 58px; width: 200px; height: 150px;
    background: linear-gradient(160deg, var(--sample-blue), #0e2b38 70%, #9aa5ab);
  }
  .headline {
    position: absolute; left: 22px; top: 116px;
    font-family: "Archivo Black", "Arial Black", sans-serif;
    color: var(--shine-yellow);
    font-size: 27px; line-height: 0.95; letter-spacing: 0.5px;
    text-transform: uppercase; font-weight: 400;
  }
  .order-line {
    position: absolute; left: 22px; top: 252px;
    color: var(--shine-yellow); font-weight: 700; font-size: 14px; line-height: 1.15;
  }
  .specials {
    position: absolute; left: 22px; top: 292px; list-style: none;
    font-size: 9.5px; line-height: 1.3; color: var(--text-soft);
  }
  .specials li::before { content: "\2714\00a0\00a0"; font-size: 8px; }
  .logo-name {
    font-family: "Arimo", Arial, sans-serif; font-weight: 700; color: var(--text-white);
  }
  .postcard--front .logo-name {
    position: absolute; right: 26px; top: 262px; font-size: 20px;
  }

  /* Back */
  .service-field {
    position: absolute; left: -30px; right: -30px; top: 2px; bottom: 0;
    color: var(--word-grey); font-weight: 700; opacity: .55;
    line-height: 1.05; word-spacing: 6px; white-space: nowrap;
  }
  .service-field p:nth-child(odd) { font-size: 17px; }
  .service-field p:nth-child(even) { font-size: 13px; margin-left: -40px; }
  .service-field p:nth-child(3n) { font-size: 21px; color: var(--word-light); }
  .postage-stamp {
    position: absolute; right: 40px; top: 26px; width: 46px; height: 50px;
    background: var(--text-white); color: var(--stamp-ink);
    font-size: 8px; text-align: center; padding-top: 14px; line-height: 1.1;
  }
  .logo-band {
    position: absolute; left: 0; right: 0; bottom: 0; height: 92px;
    background: linear-gradient(180deg, rgba(21,21,21,0), var(--band-dark) 35%);
  }
  .postcard--back .logo-name {
    position: absolute; right: 26px; bottom: 30px; font-size: 22px;
  }
</style>
</head>
<body>
<main class="stage">

  <section class="postcard postcard--front">
    <div class="samples">
      <div class="sample sample--wedding" role="img" aria-label="Sample save-the-date postcard with an engagement ring"></div>
      <div class="sample sample--beauty" role="img" aria-label="Sample beauty postcard with a smiling woman"></div>
      <div class="sample sample--auto" role="img" aria-label="Sample auto detailing postcard with a silver car"></div>
    </div>
    <h1 class="headline">Let us<br>make<br>your<br>buissness<br>shine !</h1>
    <p class="order-line">24 hr/7 Day<br>orders@inkwillow.com</p>
    <ul class="specials">
      <li>Double your order FREE (order 500 business cards and get 1000)</li>
      <li>250 100lb gloss stock brochures 99.00</li>
      <li>Business packages (cards, envelopes and letterhead) 299</li>
      <li>1000 flyers 140.40</li>
      <li>5000 postcards 179.99</li>
    </ul>
    <p class="logo-name">InkWillow</p>
  </section>

  <section class="postcard postcard--back">
    <div class="service-field" aria-hidden="true">
      <p>banners booklets brochures business cards calendars catalogs CD/DVD packages envelopes</p>
      <p>event tickets flyers hangtags postcards posters presentation folders rack cards labels</p>
      <p>table tents window cling and decal banners booklets brochures business cards</p>
      <p>calendars catalogs CD/DVD packages envelopes event tickets flyers hangtags postcards</p>
      <p>posters presentation folders rack cards labels table tents window cling and decal</p>
      <p>brochures business cards calendars catalogs CD/DVD packages envelopes event tickets</p>
      <p>flyers hangtags postcards posters presentation folders rack cards labels table tents</p>
      <p>window cling and decal banners booklets brochures business cards calendars catalogs</p>
      <p>CD/DVD packages envelopes event tickets flyers hangtags postcards posters labels</p>
      <p>presentation folders rack cards labels table tents window cling and decal banners</p>
      <p>booklets brochures business cards calendars catalogs CD/DVD packages envelopes</p>
      <p>event tickets flyers hangtags postcards posters presentation folders rack cards</p>
      <p>labels table tents window cling and decal banners booklets brochures business cards</p>
      <p>calendars catalogs CD/DVD packages envelopes event tickets flyers hangtags postcards</p>
      <p>posters presentation folders rack cards labels table tents window cling and decal</p>
      <p>banners booklets brochures business cards calendars catalogs CD/DVD packages</p>
      <p>envelopes event tickets flyers hangtags postcards posters presentation folders</p>
      <p>rack cards labels table tents window cling and decal banners booklets brochures</p>
      <p>business cards calendars catalogs CD/DVD packages envelopes event tickets flyers</p>
      <p>hangtags postcards posters presentation folders rack cards labels table tents</p>
    </div>
    <div class="postage-stamp">Postage<br>Stamp</div>
    <div class="logo-band"></div>
    <p class="logo-name">InkWillow</p>
  </section>

</main>
</body>
</html>
```